RW Holloway LLC Business Card - Civil Engineering & Consulting Firm

We need a Business Card that is elegant, and masculine.  It is our Professional Civil Engineering & Consulting Company located in San Antonio TX (Not s construction or builder firm- no gears & no tool images please). We provide civil engineering services including  commercial site plans, grading and drainage plans, utility plans, hydraulics and hydrology, land planning, utility coordination, and other general civil engineering services related to commercial and residential development.
We have 2 existing Logos. We would like to convey reliability, strength, trustworthiness and attention to detail.  Blues and orange tones as per logo We are OK with the use of a darker blue in the mix.  We have 2 logo versions - Full Company Name Logo to go on the back of card, & Small Icon Logo for the front w/ personal Info.

Target Market(s)
Architects, Real Estate Developers, Other Strctural Engineers, Surveyers, General Contractors
Industry/Entity Type
Professional Civil Engineering
Contact Information for Business Card
Name, Position, Address, Cell & Office #, email, and company website
Font styles to use
Other font styles liked:
- Avian
Requirements
Should not have
- No Tools, No Gears, no Cranes, or Construction Equipment.

```html
<!DOCTYPE html>
<html lang="en">
<head>
<meta charset="utf-8">
<title>RW Holloway LLC – Business Card</title>
<link href="https://fonts.googleapis.com/css2?family=Lato:wght@400;700&family=Oswald:wght@500&display=swap" rel="stylesheet">
<style>
  :root {
    --page-bg: #1c1c1e;
    --card-bg: #111214;
    --accent-blue: #78acdc;
    --accent-orange: #f39123;
    --text-light: #f2f2f2;
    --divider: #8a8a8a;
  }
  * { box-sizing: border-box; margin: 0; padding: 0; }
  html, body { width: 1200px; height: 900px; overflow: hidden; }
  body {
    background: var(--page-bg);
    font-family: "Lato", sans-serif;
    display: flex;
    flex-direction: column;
    align-items: center;
    justify-content: center;
    gap: 36px;
  }
  .card {
    position: relative;
    width: 700px;
    height: 400px;
    background: var(--card-bg);
    box-shadow: 0 10px 30px rgba(0,0,0,0.55);
    overflow: hidden;
  }
  .card::after {
    content: "";
    position: absolute;
    left: 0; right: 0; bottom: 0;
    height: 15px;
    background: var(--accent-blue);
  }
  .card--front, .card--back { width: 640px; height: 400px; }
  body { gap: 30px; }
  .card { height: 385px; }

  /* Front: company name */
  .company-mark {
    position: absolute;
    inset: 0 0 15px 0;
    display: flex;
    align-items: center;
    justify-content: center;
  }
  .company-name {
    font-family: "Lato", sans-serif;
    font-weight: 400;
    font-size: 52px;
    letter-spacing: 4px;
    color: var(--accent-blue);
    text-transform: uppercase;
  }

  /* Back: personal details */
  .person {
    position: absolute;
    left: 70px;
    top: 150px;
    width: 230px;
  }
  .person-name {
    font-family: "Oswald", sans-serif;
    font-weight: 500;
    font-size: 34px;
    line-height: 1;
    text-transform: uppercase;
    letter-spacing: -0.5px;
    white-space: nowrap;
  }
  .person-name .first { color: var(--accent-blue); }
  .person-name .last { color: var(--accent-orange); }
  .person-role {
    margin-top: 4px;
    font-size: 18px;
    color: var(--text-light);
    text-align: right;
  }
  .divider {
    position: absolute;
    left: 330px;
    top: 140px;
    width: 1px;
    height: 86px;
    background: var(--divider);
  }
  .contacts {
    position: absolute;
    left: 352px;
    top: 146px;
    list-style: none;
  }
  .contacts li {
    display: flex;
    align-items: center;
    gap: 9px;
    font-size: 19px;
    color: var(--text-light);
    line-height: 26px;
  }
  .contacts svg { width: 18px; height: 18px; flex: none; }
  .address {
    position: absolute;
    left: 70px;
    bottom: 52px;
    font-size: 20px;
    color: var(--text-light);
  }
</style>
</head>
<body>
  <section class="card card--front" aria-label="Card front">
    <div class="company-mark">
      <span class="company-name">RW Holloway LLC</span>
    </div>
  </section>

  <section class="card card--back" aria-label="Card back">
    <div class="person">
      <h1 class="person-name"><span class="first">Marcus</span> <span class="last">Whitfield</span></h1>
      <p class="person-role">Managing Director</p>
    </div>
    <div class="divider"></div>
    <ul class="contacts">
      <li>
        <svg viewBox="0 0 24 24" aria-hidden="true"><path fill="none" stroke="var(--accent-blue)" stroke-width="2" d="M6 3l3 4-2 2c1 3 4 6 7 7l2-2 4 3-2 3C10 20 4 14 3 5z"/></svg>
        210-555 0147
      </li>
      <li>
        <svg viewBox="0 0 24 24" aria-hidden="true"><rect x="2" y="5" width="20" height="14" fill="none" stroke="var(--accent-blue)" stroke-width="2"/><path d="M2 5l10 8 10-8" fill="none" stroke="var(--accent-blue)" stroke-width="2"/></svg>
        info@rwholloway.com
      </li>
      <li>
        <svg viewBox="0 0 24 24" aria-hidden="true"><g fill="none" stroke="var(--accent-blue)" stroke-width="1.8"><circle cx="12" cy="12" r="9"/><ellipse cx="12" cy="12" rx="4" ry="9"/><path d="M3 12h18M5 7h14M5 17h14"/></g></svg>
        www.rwholloway.com
      </li>
    </ul>
    <p class="address">118, Ridge Park Drive, San Antonio, 78230</p>
  </section>
</body>
</html>
```